Profesional personal website needs design and business card

I need a business card with my professional name as a logo "Dorian Vitality" for my business. I am a Wellness Coach, consultant and trainer. So it should be professional, wellness oriented and modern.

Target Market(s)

Private clients, governments, corporations. Luxury and high market.

Industry/Entity Type

Health And Wellness

Contact Information for Business Card

Dorian Vitality should be the logo

Colors

Designer to choose colors to be used in the design.

Requirements
Must have
• Dorian Vitality
• Name: Tomás Lirandel
• Wellness Coach, Consultant & Trainer.
• Website: www.dorianvitality-example.com
• Phone:
• Spain (+34) 612 480 317
• (USA) +1 (555) 610 4829
Nice to have
• The most important is the design of "Dorian Vitality", as this is going to be my personal brand logo. It should be professional, wellness, high end and actual.
Should not have
• no golds, no baroque style..

```html
<!DOCTYPE html>
<html lang="en">
<head>
<meta charset="utf-8">
<title>Dorian Vitality — Business Card</title>
<link rel="stylesheet" href="https://fonts.googleapis.com/css2?family=Arimo:wght@400;700&display=swap">
<style>
  :root {
    --page-bg: #e6e7ea;
    --card-white: #f7f7f5;
    --teal: #4e9e9a;
    --teal-light: #62aaa6;
    --grey-top: #8d8e97;
    --grey-bottom: #696a73;
    --text-light: #ffffff;
  }
  * { margin: 0; padding: 0; box-sizing: border-box; }
  html, body {
    width: 1200px;
    height: 936px;
    overflow: hidden;
    background: var(--page-bg);
    font-family: "Arimo", Arial, sans-serif;
  }
  .card {
    position: absolute;
    left: 100px;
    top: 168px;
    width: 1000px;
    height: 600px;
    background: var(--card-white);
    box-shadow: 0 10px 30px rgba(0,0,0,0.12);
    overflow: hidden;
  }
  .card-shapes {
    position: absolute;
    inset: 0;
    width: 1000px;
    height: 600px;
  }
  .brand {
    position: absolute;
    left: 62px;
    top: 120px;
  }
  .brand-name {
    font-weight: 700;
    font-size: 46px;
    letter-spacing: 2px;
    color: var(--teal);
    white-space: nowrap;
    line-height: 1;
  }
  .person {
    position: absolute;
    right: 32px;
    top: 336px;
    text-align: right;
  }
  .person-name {
    font-weight: 700;
    font-size: 36px;
    color: var(--teal-light);
    letter-spacing: 0.5px;
    line-height: 1;
  }
  .person-role {
    margin-top: 10px;
    font-size: 22px;
    color: var(--text-light);
    line-height: 1;
  }
  .contacts {
    position: absolute;
    right: 34px;
    top: 444px;
    list-style: none;
  }
  .contact {
    display: flex;
    justify-content: flex-end;
    align-items: center;
    gap: 14px;
    height: 38px;
    font-size: 23px;
    color: var(--text-light);
  }
  .contact-icon {
    width: 22px;
    height: 22px;
    flex: none;
  }
</style>
</head>
<body>
  <div class="card">
    <svg class="card-shapes" viewBox="0 0 1000 600" aria-hidden="true">
      <defs>
        <linearGradient id="greyBand" x1="0" y1="0" x2="0" y2="1">
          <stop offset="0" stop-color="var(--grey-top)"/>
          <stop offset="1" stop-color="var(--grey-bottom)"/>
        </linearGradient>
      </defs>
      <path class="grey-band" fill="url(#greyBand)"
            d="M0,440 C230,478 400,430 600,330 C750,262 900,258 1000,262 L1000,600 L0,600 Z"/>
      <path class="teal-swoosh" fill="var(--teal-light)"
            d="M0,368 C200,440 380,432 560,336 C700,266 810,254 875,256 C790,262 700,290 575,350 C400,428 200,448 0,402 Z"/>
    </svg>

    <div class="brand">
      <div class="brand-name">Dorian Vitality</div>
    </div>

    <div class="person">
      <div class="person-name">TOMÁS LIRANDEL</div>
      <div class="person-role">Wellness Coach, Consultant &amp; Trainer</div>
    </div>

    <ul class="contacts">
      <li class="contact">
        <span>+34 612 480 317</span>
        <svg class="contact-icon" viewBox="0 0 24 24" aria-hidden="true">
          <circle cx="12" cy="12" r="10" fill="none" stroke="var(--teal-light)" stroke-width="1.6"/>
          <path d="M8.5 7.5c.6-.6 1.3-.5 1.6.1l.8 1.6c.2.5 0 .9-.3 1.2l-.5.5c.6 1.3 1.6 2.3 2.9 2.9l.5-.5c.3-.3.8-.5 1.2-.3l1.6.8c.6.3.7 1 .1 1.6-1 1-2.6 1.1-4.4-.1-1.5-1-2.9-2.4-3.9-3.9-1.200-1.8-1.1-3.4-.1-4.4z" fill="var(--teal-light)"/>
        </svg>
      </li>
      <li class="contact">
        <span>+1 (555) 610 4829</span>
        <svg class="contact-icon" viewBox="0 0 24 24" aria-hidden="true">
          <circle cx="12" cy="12" r="10" fill="none" stroke="var(--teal-light)" stroke-width="1.6"/>
          <path d="M8.5 7.5c.6-.6 1.3-.5 1.6.1l.8 1.6c.2.5 0 .9-.3 1.2l-.5.5c.6 1.3 1.6 2.3 2.9 2.9l.5-.5c.3-.3.8-.5 1.2-.3l1.6.8c.6.3.7 1 .1 1.6-1 1-2.6 1.1-4.4-.1-1.5-1-2.9-2.4-3.9-3.9-1.2-1.8-1.1-3.4-.1-4.4z" fill="var(--teal-light)"/>
        </svg>
      </li>
      <li class="contact">
        <span>www.dorianvitality-example.com</span>
        <svg class="contact-icon" viewBox="0 0 24 24" aria-hidden="true">
          <circle cx="12" cy="12" r="10" fill="var(--teal-light)"/>
          <g fill="none" stroke="var(--grey-bottom)" stroke-width="1.2">
            <ellipse cx="12" cy="12" rx="4.5" ry="10"/>
            <line x1="2" y1="12" x2="22" y2="12"/>
            <path d="M4 7h16M4 17h16"/>
          </g>
        </svg>
      </li>
    </ul>
  </div>
</body>
</html>
```